Cyber security firm needs to have a new look and modren website design

Vantrel Corp is already established and looking to improve the feel and UI of the site and cause potential clients to say "wow, let's contact them".
We provide cybersecurity assessment consulting services helping our clients to feel safer than they are now with a straightforward approach to data safety, as the current frameworks and regulations are NOT affective anymore.

the current site is: www.vantrel.biz

Please check the following sites:
qolbarix.com
tramview-north.com
https://www.delmoquin.com

HomePage Design:
In general: we want to tell the viewer that it's a digital war out there, which is not a simple one. If not taking care of it will have causalities: https://www.delmoquin.com/ see picture? See that and some what I'm afraid.... I need some assurance and safety...
1. Do not use the existing site content / design.
2. Do not use the 3 simple steps
3. Have slides top as it is now:
A Hacker Is Knocking, Are You READY? (and a matching picture)
4. Contact form on the right
5. 4 block services:
Web Application Security.
Internal / External Vulnerability Assessments.
Penetration Testing.
Malware Attack Simulation.
6. Recent News: 3 Blocks
7. Recent Posts: 3 Blocks
8. Under the contact form: Download out FREE Report Cybersecurity Assessment Framework
9. Top contact form search line.
10. Bottom page should show all links from top menu
11. This design should work on WordPress

Thanks.

Target Market(s)

Right now: Financials.
Looking to have to add more, will decide later.

Industry/Entity Type

Security

Coding

Coded - Design and coding required

Number of Pages Required

5+ page

Font styles to use
Other font styles liked:
• Caliberi

Requirements
Must have
• Our site is based on CMS: WordPress
• Should be progressive: to be showed on any device: PC, tablets and phones.
• Browsers: IE, Chrome and Firefox.
• Look serious, experts in their field and getting tasks done!
• Use the same fonts from:
• qolbarix.com
• tramview-north.com
• https://www.delmoquin.com

```html
<!DOCTYPE html>
<html lang="en">
<head>
<meta charset="utf-8">
<title>Vantrel Corp — Cybersecurity Assessment</title>
<link rel="stylesheet" href="https://fonts.googleapis.com/css2?family=Roboto:wght@400;500;700&family=Roboto+Condensed:wght@700&display=swap">
<style>
:root{
  --red:#c8202a;
  --navy:#173f63;
  --ink:#222629;
  --text:#4a4f55;
  --muted:#777d84;
  --light:#eeeff1;
  --circle:#e6e7e9;
  --footer:#0e4a72;
  --footer-deep:#0a3a5b;
  --white:#ffffff;
}
*{box-sizing:border-box;margin:0;padding:0}
html,body{width:1200px;height:2455px;overflow:hidden}
body{font-family:"Roboto",Arial,sans-serif;color:var(--text);background:var(--white);position:relative}
a{color:inherit;text-decoration:none}

/* header */
.top-rule{height:8px;background:var(--red)}
.site-header{height:82px;position:relative;background:var(--white)}
.brand{position:absolute;left:87px;top:22px;display:flex;align-items:center;gap:12px}
.brand-dot{width:34px;height:34px;border-radius:50%;background:var(--navy)}
.brand-name{font-weight:700;font-size:36px;line-height:38px;color:var(--navy);letter-spacing:.5px}
.main-nav{position:absolute;left:404px;top:20px;display:flex;gap:2px;align-items:center}
.main-nav a{font-size:15px;color:var(--ink);padding:9px 11px;border-radius:3px;white-space:nowrap}
.main-nav a.is-active{background:var(--red);color:var(--white)}
.search{position:absolute;left:940px;top:22px;width:173px;height:34px;border:1px solid #d8dadd;border-radius:3px;display:flex;align-items:center;padding:0 12px;font-size:14px;color:#9aa0a6;justify-content:space-between}

/* hero */
.hero{position:relative;height:497px;background:linear-gradient(100deg,#0b1522 0%,#16314f 35%,#3f6f98 55%,#1a3654 75%,#0c1624 100%)}
.slide-arrow{position:absolute;top:226px;width:50px;height:50px;border-radius:50%;background:var(--white);display:flex;align-items:center;justify-content:center}
.slide-arrow.prev{left:84px}
.slide-arrow.next{left:1062px}

/* intro */
.intro{background:var(--light);height:258px;position:relative}
.intro h2{position:absolute;left:87px;top:30px;font-size:24px;color:var(--red);font-weight:700}
.intro p{position:absolute;left:87px;top:74px;width:530px;font-size:14px;line-height:24px;color:var(--text)}
.btn{display:inline-block;background:var(--red);color:var(--white);font-size:13px;font-weight:500;padding:10px 18px;border-radius:2px}
.intro .btn{position:absolute;left:87px;top:190px}
.intro-image{position:absolute;left:665px;top:35px;width:448px;height:188px;background:linear-gradient(135deg,#1d4f8c,#3d7fc4 50%,#d6a431 62%,#2a5fa0 80%)}

/* services */
.services{height:442px;position:relative;text-align:center}
.services h2{position:absolute;top:42px;width:100%;font-size:24px;color:var(--red);font-weight:700}
.services .lead{position:absolute;top:80px;left:330px;width:540px;font-size:12px;line-height:18px;color:var(--muted)}
.service{position:absolute;top:142px;width:210px}
.service .icon{width:132px;height:132px;border-radius:50%;background:var(--circle);margin:0 auto;display:flex;align-items:center;justify-content:center}
.service.is-featured .icon{background:var(--navy)}
.service h3{margin-top:14px;font-size:15px;line-height:20px;color:var(--red);font-weight:500}
.service p{margin:4px auto 0;width:170px;font-size:12px;line-height:17px;color:var(--muted);padding-bottom:8px;border-bottom:3px solid var(--red)}

/* disasters band */
.prepare{height:262px;background:linear-gradient(180deg,#2f333a,#24272c);position:relative;text-align:center;color:var(--white)}
.prepare h2{position:absolute;top:52px;width:100%;font-family:"Roboto Condensed",Arial,sans-serif;font-size:34px;line-height:40px;text-decoration:underline;text-underline-offset:6px}
.prepare p{position:absolute;top:112px;left:340px;width:520px;font-size:13px;line-height:20px;font-weight:500}
.prepare .btn{position:absolute;top:180px;left:552px}

/* recent */
.recent{height:464px;position:relative}
.recent-col{position:absolute;top:40px;width:470px}
.recent-col.news{left:87px}
.recent-col.posts{left:633px}
.recent-col h2{font-size:22px;font-weight:500;color:var(--red);padding-bottom:8px;border-bottom:1px solid #dcdde0;margin-bottom:18px}
.divider{position:absolute;left:597px;top:40px;width:1px;height:390px;background:#dcdde0}
.entry{display:flex;gap:14px;height:105px;margin-bottom:18px}
.entry .thumb{width:131px;height:100px;flex:none}
.entry h3{font-size:16px;font-weight:500;color:var(--red)}
.entry .date{font-size:11px;color:var(--muted);margin-top:3px}
.entry p{font-size:13px;line-height:19px;color:var(--text);margin-top:4px}
.entry .more{font-size:11px;color:var(--red)}

/* partners */
.partners{height:128px;display:flex;align-items:center;justify-content:space-between;padding:0 87px;border-top:1px solid #e4e5e7}
.badge{height:46px;border-radius:4px;background:#d4d8dc}

/* footer */
.site-footer{height:281px;background:var(--footer);color:var(--white);position:relative}
.site-footer h2{position:absolute;top:36px;font-size:20px;font-weight:500;white-space:nowrap}
.footer-contact{position:absolute;left:87px;top:0;width:300px}
.footer-contact h2{left:0}
.contact-list{position:absolute;left:87px;top:82px;list-style:none;font-size:12px;line-height:18px}
.contact-list li{display:flex;gap:14px;align-items:flex-start;margin-bottom:10px}
.contact-list svg{flex:none;margin-top:1px}
.footer-brand{position:absolute;left:87px;top:200px;font-weight:700;font-size:32px}
.consult{position:absolute;left:496px;top:0;width:300px}
.consult h2{left:0}
.consult .note{position:absolute;top:76px;width:260px;font-size:12px;line-height:17px;font-weight:500}
.field{position:absolute;left:0;width:227px;height:33px;border:1px solid #7aa3c3;background:#2e6590;font-size:12px;color:#d6e3ee;padding:9px 10px}
.send{position:absolute;left:0;top:214px;background:#e9ecef;color:var(--ink);font-size:12px;padding:9px 18px;border-radius:2px}
.social{position:absolute;left:990px;top:0;width:160px}
.social h2{left:0}
.social ul{position:absolute;top:90px;list-style:none;width:160px}
.social li{display:flex;align-items:center;gap:12px;font-size:14px;margin-bottom:14px}
.social .disc{width:34px;height:34px;border-radius:50%;background:#d5dee6}
.legal{position:absolute;left:0;top:2422px;width:1200px;height:33px;background:var(--footer-deep);color:#c9d6e1;font-size:11px;display:flex;align-items:center;justify-content:space-between;padding:0 87px}
.legal nav{display:flex;gap:32px}
</style>
</head>
<body>
<div class="top-rule"></div>
<header class="site-header">
  <div class="brand"><span class="brand-dot"></span><span class="brand-name">Vantrel</span></div>
  <nav class="main-nav">
    <a class="is-active" href="#">Home</a><a href="#">About</a><a href="#">Service</a><a href="#">Partners</a><a href="#">Event</a><a href="#">Media</a><a href="#">Contact us</a>
  </nav>
  <div class="search"><span>Search</span>
    <svg width="14" height="14" viewBox="0 0 14 14"><circle cx="6" cy="6" r="4.5" fill="none" stroke="#666" stroke-width="1.6"/><line x1="9.5" y1="9.5" x2="13" y2="13" stroke="#666" stroke-width="1.6"/></svg>
  </div>
</header>

<section class="hero" role="img" aria-label="Analysts in a dark operations room touching glowing panels labelled confidentiality, availability and integrity">
  <a class="slide-arrow prev" href="#" aria-label="Previous slide"><svg width="16" height="16" viewBox="0 0 16 16"><path d="M10 3 5 8l5 5" fill="none" stroke="#222" stroke-width="2.4"/></svg></a>
  <a class="slide-arrow next" href="#" aria-label="Next slide"><svg width="16" height="16" viewBox="0 0 16 16"><path d="M6 3l5 5-5 5" fill="none" stroke="#222" stroke-width="2.4"/></svg></a>
</section>

<section class="intro">
  <h2>Hacker Is Knocking, Are You READY?</h2>
  <p>Lorem Ipsum is simply dummy text of the printing and typesetting industry. Lorem Ipsum has been the industry's standard dummy text ever since the 1500s, when an unknown printer took a galley of type and scrambled it to make a type specimen book. It has survived not only five centu</p>
  <a class="btn" href="#">Read More</a>
  <div class="intro-image" role="img" aria-label="Golden padlock resting on a blue circuit board"></div>
</section>

<section class="services">
  <h2>Lorem ipsum dolor sit amet</h2>
  <p class="lead">"Lorem ipsum dolor sit amet, consectetur adipiscing elit, sed do eiusmod tempor incididunt ut labore et dolore magna aliqua. Ut enim ad minim veniam, quis nostrud exercitation ullamco laboris.</p>
  <div class="service is-featured" style="left:70px">
    <div class="icon"><svg width="50" height="56" viewBox="0 0 50 56"><path d="M25 2 4 10v16c0 14 9 24 21 28 12-4 21-14 21-28V10z" fill="#fff"/><path d="M25 8v40c9-4 15-11 15-22V13z" fill="#173f63"/></svg></div>
    <h3>Web Application Security</h3>
    <p>Lorem Ipsum is simply dummy text of the printing and typesetting industry. Lorem Ipsum has been the industry's standard...</p>
  </div>
  <div class="service" style="left:372px">
    <div class="icon"><svg width="50" height="50" viewBox="0 0 50 50" fill="#3a3f45"><circle cx="14" cy="13" r="6"/><circle cx="36" cy="13" r="6"/><circle cx="25" cy="37" r="7"/><path d="M14 13 25 37 36 13" fill="none" stroke="#3a3f45" stroke-width="4"/></svg></div>
    <h3>Internal / External Vulnerability Assessments</h3>
    <p>Lorem Ipsum is simply dummy text of the printing and typesetting industry Lorem Ipsum</p>
  </div>
  <div class="service" style="left:637px">
    <div class="icon"><svg width="44" height="52" viewBox="0 0 44 52"><path d="M10 22V15a12 12 0 0 1 24 0v7" fill="none" stroke="#3a3f45" stroke-width="5"/><rect x="4" y="22" width="36" height="28" rx="3" fill="#3a3f45"/></svg></div>
    <h3>Penetration Testing</h3>
    <p>Lorem Ipsum is simply dummy text of the printing and typesetting industry. Lorem Ipsum has been the industry's standard...</p>
  </div>
  <div class="service" style="left:926px">
    <div class="icon"><svg width="54" height="48" viewBox="0 0 54 48"><rect x="3" y="3" width="48" height="32" rx="2" fill="none" stroke="#3a3f45" stroke-width="4"/><rect x="19" y="38" width="16" height="4" fill="#3a3f45"/><rect x="12" y="42" width="30" height="4" fill="#3a3f45"/><circle cx="27" cy="19" r="7" fill="#3a3f45"/></svg></div>
    <h3>Malware Attack Simulation</h3>
    <p>Lorem Ipsum is simply dummy text of the printing and typesetting industry. Lorem Ipsum has been the industry's standard...</p>
  </div>
</section>

<section class="prepare">
  <h2>Are You Prepared for Disasters?</h2>
  <p>Lorem Ipsum is simply dummy text of the printing and typesetting industry. Lorem Ipsum has been the industry's standard dummy text ever since the 1500s.</p>
  <a class="btn" href="#">Learn More</a>
</section>

<section class="recent">
  <div class="recent-col news">
    <h2>Recent News</h2>
    <article class="entry"><div class="thumb" role="img" aria-label="Person typing at a laptop in a dark room" style="background:linear-gradient(135deg,#0d1a2c,#2d4f78)"></div><div><h3>Lorem Ipsum</h3><p>Lorem Ipsum is simply dummy text of the printing and typesetting industry. Lorem Ipsum has been the industry's standard dummy text ever since.</p><a class="more" href="#">Read more</a></div></article>
    <article class="entry"><div class="thumb" role="img" aria-label="Blue binary code on a screen" style="background:linear-gradient(135deg,#0a2a5c,#2f6fc0)"></div><div><h3>Lorem Ipsum</h3><p>Lorem Ipsum is simply dummy text of the printing and typesetting industry. Lorem Ipsum has been the industry's standard dummy text ever since.</p><a class="more" href="#">Read more</a></div></article>
    <article class="entry"><div class="thumb" role="img" aria-label="Hooded figure with a yellow warning folder" style="background:linear-gradient(135deg,#111318,#3a3d2a 60%,#b59a2a)"></div><div><h3>Lorem Ipsum</h3><p>Lorem Ipsum is simply dummy text of the printing and typesetting industry. Lorem Ipsum has been the industry's standard dummy text ever since.</p><a class="more" href="#">Read more</a></div></article>
  </div>
  <div class="divider"></div>
  <div class="recent-col posts">
    <h2>Recent Posts</h2>
    <article class="entry"><div class="thumb" role="img" aria-label="Keyboard key labelled for cyber security" style="background:linear-gradient(135deg,#1d4d78,#6fa6d3)"></div><div><h3>Lorem Ipsum</h3><div class="date">24.08.2015</div><p>Lorem Ipsum is simply dummy text of the printing and typesetting industry. Lorem Ipsum has been the industry's standard dummy text ever since. <a class="more" href="#">Read more</a></p></div></article>
    <article class="entry"><div class="thumb" role="img" aria-label="Hands typing on a laptop keyboard" style="background:linear-gradient(135deg,#6b4a2e,#d9b48a)"></div><div><h3>Lorem Ipsum</h3><div class="date">24.08.2015</div><p>Lorem Ipsum is simply dummy text of the printing and typesetting industry. Lorem Ipsum has been the industry's standard dummy text ever since. <a class="more" href="#">Read more</a></p></div></article>
    <article class="entry"><div class="thumb" role="img" aria-label="Red stop sign over a keyboard" style="background:linear-gradient(135deg,#2a2e35,#b3262d 55%,#3a3f47)"></div><div><h3>Lorem Ipsum</h3><div class="date">24.08.2015</div><p>Lorem Ipsum is simply dummy text of the printing and typesetting industry. Lorem Ipsum has been the industry's standard dummy text ever since. <a class="more" href="#">Read more</a></p></div></article>
  </div>
</section>

<section class="partners" aria-label="Partners">
  <div class="badge" style="width:180px"></div>
  <div class="badge" style="width:165px"></div>
  <div class="badge" style="width:170px"></div>
  <div class="badge" style="width:195px"></div>
  <div class="badge" style="width:183px"></div>
</section>

<footer class="site-footer">
  <div class="footer-contact"><h2>Contact us</h2></div>
  <ul class="contact-list">
    <li><svg width="14" height="18" viewBox="0 0 14 18"><path d="M7 0a7 7 0 0 0-7 7c0 5 7 11 7 11s7-6 7-11a7 7 0 0 0-7-7z" fill="#fff"/><circle cx="7" cy="7" r="2.5" fill="#0e4a72"/></svg><span>42 Larkmoor Lane 3rd Floor<br>Brenton, BT 20417</span></li>
    <li><svg width="14" height="16" viewBox="0 0 14 16"><path d="M3 0h3l1 4-2 2c1 2 2 3 4 4l2-2 3 1v3c0 2-1 3-3 3C5 15 0 10 0 3 0 1 1 0 3 0z" fill="#fff"/></svg><span>1-555-014-2290</span></li>
    <li><svg width="16" height="12" viewBox="0 0 16 12"><rect width="16" height="12" rx="1" fill="#fff"/><path d="M1 1l7 6 7-6" fill="none" stroke="#0e4a72" stroke-width="1.5"/></svg><span>hello@vantrel.biz</span></li>
  </ul>
  <div class="footer-brand">Vantrel</div>

  <div class="consult">
    <h2>FREE Consultation!</h2>
    <p class="note">Download out FREE Report Cybersecurity Assessment Framework</p>
    <div class="field" style="top:128px">Name</div>
    <div class="field" style="top:170px">Email</div>
    <a class="send" href="#">Send</a>
  </div>

  <div class="social">
    <h2>Social Media</h2>
    <ul>
      <li><span class="disc"></span>Friendnet</li>
      <li><span class="disc"></span>Chirpline</li>
      <li><span class="disc"></span>Searchly</li>
    </ul>
  </div>
</footer>
<div class="legal">
  <span>© All rights reserved Vantrel Corp 2003-2015</span>
  <nav><a href="#">Home</a><a href="#">About</a><a href="#">Service</a><a href="#">Partners</a><a href="#">Event</a><a href="#">Media</a><a href="#">Contact us</a></nav>
</div>
</body>
</html>
```